Logistics Website Design

See website https://tqfreightglobal.com for theme and color details. Need the site to be re-done and reflect some of the designs shown in this list here: https://pixelvane.com/tags/logistics-company-website

Target Market(s)

Logistics & Transportation

Industry/Entity Type

Logistics and Supply Chain

Coding

Number of Pages Required

5+ page

Requirements
Must have
• Colors must match theme of logo. Looking for a sleek, interactive design.

```html
<!DOCTYPE html>
<html lang="en">
<head>
<meta charset="utf-8">
<title>TQ Freight Global — Delivering Strength in Every Mile</title>
<link href="https://fonts.googleapis.com/css2?family=Merriweather+Sans:wght@700;800&family=Lato:wght@400;700&display=swap" rel="stylesheet">
<style>
:root{
  --orange:#e8683f;
  --orange-soft:#ec7a52;
  --brown:#3b1308;
  --ink:#1d1d1d;
  --text:#3d3d3d;
  --muted:#5a5a5a;
  --footer:#1b0c07;
  --white:#ffffff;
}
*{box-sizing:border-box;margin:0;padding:0}
html,body{width:1200px;height:3549px;overflow:hidden;background:var(--white)}
body{position:relative;font-family:"Lato",sans-serif;color:var(--text)}
.abs{position:absolute}
.heading{font-family:"Merriweather Sans",sans-serif;font-weight:800;color:var(--ink)}
.btn{position:absolute;display:flex;align-items:center;justify-content:center;border-radius:24px;color:var(--white);font-family:"Lato",sans-serif;font-weight:700;font-size:16px}
.btn-orange{background:var(--orange)}
.btn-brown{background:var(--brown)}

/* hero */
.hero{left:0;top:0;width:1200px;height:728px;background:linear-gradient(180deg,#3f5a2a 0%,#58733a 30%,#7c8660 48%,#6f6a5e 65%,#4f5a3a 85%,#3e5228 100%)}
.hero-truck{left:730px;top:200px;width:420px;height:420px;border-radius:24px;background:linear-gradient(160deg,#c9302a 0%,#a52320 45%,#5b5e66 100%);opacity:.85}
.hero-frame{left:51px;top:51px;width:1097px;height:583px;border:1px solid rgba(255,255,255,.35);border-radius:26px;background:rgba(255,255,255,.06)}
.brand{display:flex;align-items:center;gap:10px}
.brand-mark{width:44px;height:44px;border-radius:50%;background:var(--orange)}
.brand-name{font-family:"Lato",sans-serif;font-weight:700;font-size:22px;color:var(--white);line-height:1.1}
.nav{left:437px;top:95px;width:652px;height:68px;background:var(--white);border-radius:34px;display:flex;align-items:center;padding-left:28px}
.nav a{font-size:15px;color:#333;text-decoration:none;margin-right:30px}
.nav a.active{color:var(--orange);border-bottom:2px solid var(--orange);padding-bottom:2px}
.hero-title{left:110px;top:286px;font-size:46px;line-height:56px;color:var(--white);letter-spacing:.5px}
.hero-sub{left:113px;top:412px;width:560px;font-size:22px;line-height:33px;color:var(--white)}
.dots{display:flex;gap:7px}
.dots span{width:22px;height:5px;border-radius:3px;background:#bdbdbd}
.dots span.on{background:var(--white)}

/* section titles */
.section-title{width:1200px;text-align:center;font-size:35px}
.rule{width:98px;height:3px;background:var(--orange)}
.section-lead{width:1200px;text-align:center;font-size:18px;line-height:25px;color:var(--muted)}

/* services */
.card{background:var(--white);border-radius:14px;box-shadow:0 4px 18px rgba(0,0,0,.13);padding:18px}
.card-title{font-family:"Merriweather Sans",sans-serif;font-weight:700;font-size:21px;color:var(--ink)}
.card-arrow{position:absolute;width:28px;height:28px;border-radius:50%;background:var(--orange);display:flex;align-items:center;justify-content:center}
.card-photo{position:absolute;border-radius:12px}
.slider-arrow{width:26px;height:26px;border-radius:50%;display:flex;align-items:center;justify-content:center}

/* band */
.band{left:40px;top:1448px;width:1116px;height:451px;border-radius:28px;background:linear-gradient(120deg,#e96a42 0%,#e5653c 50%,#dc5d36 100%)}
.band-title{width:1116px;text-align:center;top:116px;font-size:35px;color:var(--white)}
.band-text{left:150px;top:176px;width:816px;text-align:center;font-size:18.5px;line-height:26.5px;color:var(--white)}

/* about */
.about-photo{left:112px;top:2024px;width:412px;height:422px;border-radius:22px;background:linear-gradient(180deg,#c9a27a 0%,#e6b27a 35%,#2f4a9a 60%,#2a2a2e 100%)}
.about-text{left:613px;width:474px;font-size:17.5px;line-height:28.5px;color:var(--text);text-align:justify}

/* industries */
.ind{top:2756px;width:234px;height:243px;background:var(--white);border-radius:6px;box-shadow:0 3px 14px rgba(0,0,0,.12);text-align:center;padding-top:20px}
.ind svg{display:block;margin:0 auto}
.ind h3{font-family:"Merriweather Sans",sans-serif;font-weight:700;font-size:21px;color:var(--ink);margin-top:12px}
.ind p{font-size:15px;line-height:23px;color:var(--muted);margin:10px 14px 0}
.ind.active{background:var(--orange)}
.ind.active h3,.ind.active p{color:var(--white)}
.ind-dots span{background:#8a8a8a}
.ind-dots span.on{background:var(--orange)}

/* footer */
.footer{left:0;top:3162px;width:1200px;height:387px;background:var(--footer)}
.footer-nav a{position:absolute;top:234px;font-size:16px;color:var(--white);text-decoration:none;transform:translateX(-50%)}
.footer-icon{position:absolute;top:282px;width:40px;height:40px;border-radius:6px;display:flex;align-items:center;justify-content:center;transform:translateX(-50%)}
.footer-line{position:absolute;top:363px;height:1px;background:#5c4a44}
.copy{position:absolute;top:354px;width:1200px;text-align:center;font-size:13px;color:var(--white)}
</style>
</head>
<body>

<!-- HERO -->
<section class="abs hero">
  <div class="abs hero-truck" role="img" aria-label="Photo of a red semi truck driving on a highway among green hills"></div>
  <div class="abs hero-frame"></div>
  <div class="abs brand" style="left:107px;top:130px">
    <div class="brand-mark"></div>
    <div class="brand-name">TQ Freight<br>Global</div>
  </div>
  <nav class="abs nav">
    <a class="active">Home</a><a>About Us</a><a>Services</a><a>Industries</a><a>Contact Us</a>
  </nav>
  <div class="btn btn-orange" style="left:918px;top:107px;width:158px;height:42px">Request a Quote</div>
  <h1 class="abs heading hero-title">DELIVERING STRENGTH<br>IN EVERY MILE</h1>
  <p class="abs hero-sub">Fast, secure, and reliable freight solutions designed to move your business forward—mile after mile.</p>
  <div class="btn btn-orange" style="left:110px;top:512px;width:162px;height:42px">Request a Quote</div>
  <div class="btn btn-brown" style="left:281px;top:512px;width:145px;height:42px">View Services</div>
  <div class="abs dots" style="left:562px;top:596px"><span class="on"></span><span></span><span></span></div>
</section>

<!-- SERVICES -->
<h2 class="abs heading section-title" style="left:0;top:820px">OUR SERVICES</h2>
<div class="abs rule" style="left:550px;top:870px"></div>
<p class="abs section-lead" style="top:888px">Comprehensive logistics solutions tailored to deliver efficiency, reliability,<br>and performance at every stage.</p>

<div class="abs slider-arrow" style="left:86px;top:1200px;background:#f4b8a4">
  <svg width="12" height="12" viewBox="0 0 12 12"><path d="M8 2L4 6l4 4" stroke="#fff" stroke-width="2" fill="none"/></svg>
</div>
<div class="abs slider-arrow" style="left:1088px;top:1200px;background:var(--orange)">
  <svg width="12" height="12" viewBox="0 0 12 12"><path d="M4 2l4 4-4 4" stroke="#fff" stroke-width="2" fill="none"/></svg>
</div>

<div class="abs card" style="left:127px;top:1061px;width:262px;height:266px">
  <div class="card-title" style="margin-top:4px">Flatbed</div>
  <div class="card-arrow" style="left:218px;top:16px"><svg width="12" height="12" viewBox="0 0 12 12"><path d="M3 9L9 3M4 3h5v5" stroke="#fff" stroke-width="1.6" fill="none"/></svg></div>
  <div class="card-photo" role="img" aria-label="Photo of white trucks on a highway" style="left:9px;top:57px;width:244px;height:196px;background:linear-gradient(180deg,#b9c1bf 0%,#8f9a86 45%,#55604c 100%)"></div>
</div>

<div class="abs card" style="left:423px;top:974px;width:353px;height:353px">
  <div class="card-title" style="color:var(--orange);margin-top:2px">Step Deck Transportation</div>
  <div class="card-arrow" style="left:310px;top:12px;background:#111"><svg width="12" height="12" viewBox="0 0 12 12"><path d="M3 9L9 3M4 3h5v5" stroke="#fff" stroke-width="1.6" fill="none"/></svg></div>
  <p style="font-size:15.5px;line-height:23px;color:var(--muted);margin-top:12px">Step deck trucking services support tall, heavy, specialized freight requiring height clearance and flexible loading options.</p>
  <div class="card-photo" role="img" aria-label="Photo of a red step deck trailer outside a warehouse" style="left:9px;top:144px;width:335px;height:196px;background:linear-gradient(180deg,#8fa0b4 0%,#c9c6c0 45%,#b8402f 70%,#9c9a96 100%)"></div>
</div>

<div class="abs card" style="left:810px;top:1061px;width:263px;height:266px">
  <div class="card-title" style="margin-top:4px">Dry Van</div>
  <div class="card-arrow" style="left:219px;top:16px"><svg width="12" height="12" viewBox="0 0 12 12"><path d="M3 9L9 3M4 3h5v5" stroke="#fff" stroke-width="1.6" fill="none"/></svg></div>
  <div class="card-photo" role="img" aria-label="Photo of a white dry van truck on a road under power lines" style="left:9px;top:57px;width:245px;height:196px;background:linear-gradient(180deg,#9fa6b3 0%,#c9c9c9 50%,#4a4a4a 100%)"></div>
</div>

<!-- SUPPLY CHAIN BAND -->
<section class="abs band">
  <h2 class="abs heading band-title" style="left:0;color:var(--white)">KEEPING YOUR SUPPLY CHAIN MOVING</h2>
  <div class="abs rule" style="left:509px;top:144px;background:var(--white)"></div>
  <p class="abs band-text">We deliver a comprehensive range of open-deck and specialized transportation services—including flatbed, step deck, heavy haul, and over-dimensional freight solutions. Backed by years of experience, a trusted nationwide carrier network, and a strong safety-first culture, we provide reliable, adaptable logistics support built around the unique requirements of every load.</p>
  <div class="btn btn-brown" style="left:478px;top:306px;width:160px;height:42px">Request a Quote</div>
</section>

<!-- ABOUT -->
<div class="abs about-photo" role="img" aria-label="Photo of a blue semi truck on a highway at sunset"></div>
<h2 class="abs heading" style="left:613px;top:2018px;font-size:35px">ABOUT US</h2>
<div class="abs rule" style="left:613px;top:2068px;width:170px;height:3px;background:var(--ink)"></div>
<p class="abs about-text" style="top:2096px">TQ Freight Global™ was born out of real-world experience in the fitness equipment industry. What started as a company shipping strength equipment, cardio machines, and training gear to gyms, schools, and commercial facilities quickly evolved into something bigger.</p>
<p class="abs about-text" style="top:2257px">As order volume grew and supply chains became more complex, the team developed deep expertise in coordinating freight, managing deliveries, and navigating the challenges of large-scale equipment transportation.</p>
<div class="btn btn-orange" style="left:613px;top:2399px;width:136px;height:42px">Read More</div>

<!-- INDUSTRIES -->
<h2 class="abs heading section-title" style="left:0;top:2602px">OUR INDUSTRIES</h2>
<div class="abs rule" style="left:550px;top:2651px"></div>
<p class="abs section-lead" style="top:2668px">Comprehensive logistics solutions tailored to deliver efficiency, reliability,<br>and performance at every stage.</p>

<div class="abs ind" style="left:112px">
  <svg width="60" height="60" viewBox="0 0 60 60" fill="none" stroke="#e8683f" stroke-width="2.4"><path d="M8 6v16c0 4 6 4 6 0V6M11 6v48M46 6c-6 4-6 18 0 20v28"/><circle cx="30" cy="30" r="12"/></svg>
  <h3>Food &amp; Beverage</h3>
  <p>TQ Freight provides reliable, compliant, and efficient trucking solutions for the food and beverage industry.</p>
</div>
<div class="abs ind active" style="left:360px">
  <svg width="60" height="60" viewBox="0 0 60 60" fill="none" stroke="#fff" stroke-width="2.4"><path d="M8 8h44l4 14H4zM4 22c0 5 8 5 8 0c0 5 8 5 8 0c0 5 8 5 8 0c0 5 8 5 8 0c0 5 8 5 8 0c0 5 8 5 8 0M8 28v26h44V28M16 36h12v18M34 36h12v10H34z"/></svg>
  <h3>E-commerce &amp; Retail</h3>
  <p>E-Commerce &amp; Retail Trucking Services support fast-paced logistics demands of retailers and brands.</p>
</div>
<div class="abs ind" style="left:606px">
  <svg width="60" height="60" viewBox="0 0 60 60" fill="none" stroke="#e8683f" stroke-width="2.4"><path d="M4 54h52M8 54V26l12-8v8l12-8v8l12-8V8h8v46M14 34h6M14 42h6M28 34h6M28 42h6M40 34h6M40 42h6"/></svg>
  <h3>Manufacturing</h3>
  <p>Industrial machinery and processing equipment often present unique challenges due to size, weight, and design.</p>
</div>
<div class="abs ind" style="left:854px">
  <svg width="60" height="60" viewBox="0 0 60 60" fill="none" stroke="#e8683f" stroke-width="2.4"><circle cx="32" cy="24" r="12"/><path d="M32 18v12M26 24h12M4 40c8-4 14-2 20 2h12c3 0 3 5 0 5H24M4 52c10-4 20 2 30-2l20-12c3-2 1-6-2-5l-14 7"/></svg>
  <h3>Pharma &amp; Healthcare</h3>
  <p>TQ Freight provides reliable, compliant, and efficient trucking solutions for the food and beverage industry.</p>
</div>
<div class="abs dots ind-dots" style="left:562px;top:3034px"><span class="on"></span><span></span><span></span></div>

<!-- FOOTER -->
<footer class="abs footer">
  <div class="abs brand" style="left:496px;top:66px">
    <div class="brand-mark" style="width:48px;height:48px"></div>
    <div class="brand-name">TQ Freight<br>Global</div>
  </div>
  <div class="footer-nav">
    <a style="left:349px">Home</a><a style="left:460px">About Us</a><a style="left:579px">Services</a><a style="left:701px">Industries</a><a style="left:832px">Contact Us</a>
  </div>
  <div class="footer-icon" style="left:524px;background:var(--orange)">
    <svg width="26" height="26" viewBox="0 0 24 24" fill="none" stroke="#fff" stroke-width="1.6"><circle cx="12" cy="12" r="9"/><path d="M3 12h18M12 3c3 3 3 15 0 18M12 3c-3 3-3 15 0 18"/></svg>
  </div>
  <div class="footer-icon" style="left:604px">
    <svg width="24" height="18" viewBox="0 0 24 18"><rect x="1" y="1" width="22" height="16" rx="2" fill="#fff"/><path d="M2 2l10 8 10-8" stroke="#1b0c07" stroke-width="1.6" fill="none"/></svg>
  </div>
  <div class="footer-icon" style="left:685px">
    <svg width="22" height="22" viewBox="0 0 24 24"><path d="M6.6 10.8a15 15 0 006.6 6.6l2.2-2.2c.3-.3.7-.4 1-.2 1.1.4 2.3.6 3.6.6.6 0 1 .4 1 1V20c0 .6-.4 1-1 1A17 17 0 013 4c0-.6.4-1 1-1h3.5c.6 0 1 .4 1 1 0 1.3.2 2.5.6 3.6.1.3 0 .7-.2 1z" fill="#fff"/></svg>
  </div>
  <div class="footer-line" style="left:116px;width:263px"></div>
  <div class="footer-line" style="left:824px;width:266px"></div>
  <p class="copy">Copyright © 2026 TQ Freight Global. All rights reserved.</p>
</footer>

</body>
</html>
```